Beauty Salon Mentor Illustration

Hi There, I'm Belinda and I'm a Beauty Salon owner mentor. We are needing 5 different illustration design for a beauty salon coaching business. The pictures will be used on our website next to a small description about our course out line.
Course and what the illustrations will be referring to below:
1. Launch Pad Parlour -Make your dream of owning a salon a reality.
Three options of start-up training and support, teaching must-know insights for beauty therapists who are ready to take the leap to salon owner and want to do it right. Whether you’ve been in the beauty industry a short time or forever, Launch Pad Parlour will set you up for salon success.

2. Chairs Filled Fast - Attract more clients with simple, strategic digital marketing. Chairs Filled Fast educates on the ins and outs of sponsored social media ads. With easy-to-follow video training, you’ll establish your online presence and increase salon bookings.
Learn how to show up on social media with effective strategies that work. Choose our Handled Entirely system, or learn to do it all with our DIY system.

3. Momentum Studio Plan - Transform your salon and your life. Our most tailored program, Momentum Studio Plan offers coaching memberships with Bloom Beauty Hub’s Founder- Belinda. With our results focused framework, you will upskill employees, improve the working environment of the salon and receive leading beauty industry training as we dive into the culture and mindset of your salon. With Belinda as your business mentor and biggest cheerleader get ready to achieve your business goals and move forward with rapid growth.

4. Revive Parlour Path - Successfully put your salon back on the map.
Step into today’s beauty landscape with optimised marketing and industry expertise. If your salon’s been open for a year or even twenty years, Revive Parlour Path will elevate your business, renew your love for your salon and set you up to generate more income. Stand out from the competition as you increase online presence, learn key business development processes and see real results.

5. Skillset Studio Plan - Successfully Upskill and Level Up Your Salon. Skillset Studio Plan offers three training options- In Salon, Online & Diploma of Beauty Therapy. Whether you have your own salon or want to become qualified, Bloom Beauty Hub’s- Skillset Studio Plan adds industry authority and brings specialist expertise to all level of beauty therapists.
Our coaching is based in Australia, aim at female beauty salon owners who are ready to take their business to the next level.

In the files below is just a picture of me so you know who i am. We are wanting the illusion to appeal to a wide audience.

I am the business and everyone i attract into our coaching program works closely with me.

Target Market(s)

Beauty Salon owners; women

Font styles to use
Sans Serif

Colors
fce8d3
fee3d4
fff5ef
fff3d1
f9bb94
fcca95

Requirements
Must have
• Must be relatable to the brief, designs must look great together on the website or separately on their own.
Nice to have
• Industry relatable, engaging to the eye.
Should not have
• i would prefer if there wasn't any words on the illusion

```html
<!DOCTYPE html>
<html lang="en">
<head>
<meta charset="utf-8">
<title>Beauty Salon Mentor Illustration</title>
<link href="https://fonts.googleapis.com/css2?family=Nunito:wght@800;900&family=Open+Sans:wght@400;600;700&display=swap" rel="stylesheet">
<style>
:root{
  --board:#fbe0d3;
  --ink:#231f20;
  --rose:#f2738a;
  --plum:#4a3b5c;
  --salmon:#e8a488;
  --salmon-soft:#f2c7b3;
  --peach:#fcca95;
  --peach-soft:#fde6d3;
  --cream:#f7f2ee;
  --pink:#f77891;
  --pink-soft:#f9b8c6;
  --butter:#fbf5c8;
  --butter-deep:#f3e38a;
  --coral:#f9a48f;
  --grey:#8b8584;
  --white:#ffffff;
}
*{margin:0;padding:0;box-sizing:border-box}
html,body{width:1200px;height:1026px;overflow:hidden;background:var(--board)}
body{position:relative;font-family:"Open Sans",sans-serif;color:var(--ink)}

.board-brand{position:absolute;left:23px;top:34px;font-size:12px;letter-spacing:1.5px;text-transform:uppercase;font-weight:400;color:#4a4242}
.board-title{position:absolute;left:23px;top:98px;font-size:56px;line-height:72px;font-weight:600;letter-spacing:-.5px}
.board-title .accent{color:var(--rose)}
.board-rule{position:absolute;left:24px;top:325px;width:356px;height:1.5px;background:var(--rose)}

.card{position:absolute;width:308px;height:308px;background:var(--frame);overflow:hidden;box-shadow:0 2px 4px rgba(120,70,50,.18)}
.card--narrow{width:230px}
.panel{position:absolute;inset:13px;background:var(--inner);padding:13px 14px 10px;display:flex;flex-direction:column;overflow:hidden}
.panel-deco{position:absolute;inset:0;width:100%;height:100%}
.panel>*:not(.panel-deco){position:relative}

.brand-row{display:flex;justify-content:space-between;align-items:flex-start;margin-bottom:10px}
.brand-name{font-size:5.6px;letter-spacing:.6px;text-transform:uppercase;color:#5a4e4e;margin-top:2px}
.handle{font-size:7px;color:var(--handle,#4a4242)}
.card--narrow .handle{font-size:5.6px}

.heading{font-family:"Nunito",sans-serif;font-weight:900;color:var(--head);line-height:1.05}
.subtitle{color:var(--sub);line-height:1.2;margin-top:3px}
.body-copy{font-size:8.2px;line-height:1.55;text-align:justify;color:#4d4646;letter-spacing:.1px}
.card--narrow .body-copy{font-size:6.9px;line-height:1.5}

.contact{margin-top:auto;display:flex;justify-content:space-between;font-size:6.6px;color:var(--foot,#4d4646);padding-top:6px}
.card--narrow .contact{font-size:4.6px}
.contact span{display:flex;align-items:center;gap:2px}
.contact svg{width:6px;height:6px;flex:none}
.card--narrow .contact svg{width:4.5px;height:4.5px}

.art{border-radius:50%}

/* Chairs Filled Fast */
.card--booking{--frame:var(--salmon);--inner:var(--cream);--head:var(--plum);--sub:#3e3838}
.card--booking .heading{font-size:24px;margin-top:14px}
.card--booking.card--narrow .heading{font-size:19px;margin-top:8px}
.card--booking .subtitle{font-size:11px;margin-top:4px}
.card--booking.card--narrow .subtitle{font-size:9px}
.card--booking .body-copy{margin-top:18px}
.card--booking.card--narrow .body-copy{margin-top:14px}
.card--booking .art{position:absolute;right:6px;top:0;width:90px;height:82px;background:radial-gradient(circle at 50% 55%,#f6b4bd,#e9dfd8 60%,#fff 72%)}
.card--booking.card--narrow .art{width:70px;height:62px;right:2px}

/* Launch Pad Parlour */
.card--start{--frame:var(--peach);--inner:var(--peach-soft);--head:var(--ink);--sub:var(--rose);--handle:var(--rose);--foot:var(--rose)}
.card--start .heading{font-size:19.5px;text-transform:uppercase;letter-spacing:.4px;margin-top:4px}
.card--start.card--narrow .heading{font-size:14.5px}
.card--start .subtitle{font-size:13px;font-weight:400}
.card--start.card--narrow .subtitle{font-size:10px}
.card--start .art{width:92px;height:80px;margin:10px auto 12px;background:radial-gradient(circle at 50% 40%,#f3c9a6,#d8cdbf 60%,#c8bba9)}
.card--start.card--narrow .art{width:80px;height:72px;margin:10px auto 10px}

/* Revive Parlour Path */
.card--revive{--frame:var(--salmon-soft);--inner:var(--cream);--head:var(--rose);--sub:#2f2a2a}
.card--revive .heading{font-size:19px;margin-top:4px}
.card--revive.card--narrow .heading{font-size:14px}
.card--revive .subtitle{font-size:14px;line-height:1.2;width:120px}
.card--revive.card--narrow .subtitle{font-size:12px;width:90px}
.card--revive .subtitle b{font-weight:700}
.card--revive .body-copy{margin-top:14px}
.card--revive.card--narrow .body-copy{margin-top:10px}
.card--revive .art{position:absolute;right:22px;top:50px;width:110px;height:110px;border-radius:40%;background:radial-gradient(circle at 40% 40%,#f59cb2,#f3d6a8 55%,#b9b28f 90%)}
.card--revive.card--narrow .art{right:4px;top:48px;width:70px;height:80px}

/* Skillset Studio Plan */
.card--educate{--frame:var(--pink);--inner:var(--white);--head:var(--ink);--sub:var(--grey)}
.card--educate .heading{font-size:22px;margin-top:4px}
.card--educate.card--narrow .heading{font-size:15.5px}
.card--educate .subtitle{font-size:15px}
.card--educate.card--narrow .subtitle{font-size:10.5px}
.card--educate .art{width:80px;height:70px;margin:6px 0 8px 100px;border-radius:45%;background:radial-gradient(circle at 45% 40%,#f8a6bb,#efd6b7 60%,#cfc39c)}
.card--educate.card--narrow .art{width:66px;height:58px;margin:8px 0 8px 80px}
.card--educate .body-copy{font-size:8px;line-height:1.45}
.card--educate.card--narrow .body-copy{font-size:6.7px}

/* Momentum Studio Plan */
.card--excel{--frame:#f87589;--inner:var(--butter);--head:var(--ink);--sub:var(--rose);--foot:var(--rose)}
.card--excel .heading{font-size:20.5px;margin-top:4px}
.card--excel.card--narrow .heading{font-size:15px}
.card--excel .subtitle{font-size:13.5px}
.card--excel.card--narrow .subtitle{font-size:10px}
.card--excel .art{width:76px;height:76px;margin:10px auto 12px;background:radial-gradient(circle,#dbe6ec 0 35%,#fff 36% 100%);box-shadow:0 0 0 1px #f0d9d0}
.card--excel.card--narrow .art{width:66px;height:66px;margin:8px auto 10px}
.card--excel .body-copy{font-size:8px;line-height:1.45}
.card--excel.card--narrow .body-copy{font-size:6.7px}
</style>
</head>
<body>

<div class="board-brand">Bloom Beauty Hub</div>
<h1 class="board-title">Beauty<br>Salon Mentor<br><span class="accent">Illustration</span></h1>
<div class="board-rule"></div>

<svg width="0" height="0" style="position:absolute">
  <defs>
    <symbol id="icon-phone" viewBox="0 0 10 10"><path d="M2 1l2 2-1 1c.5 1.2 1.5 2.2 3 3l1-1 2 2-1.5 1.5C4 9 1 6 .5 2.5z" fill="currentColor"/></symbol>
    <symbol id="icon-mail" viewBox="0 0 10 10"><rect x="1" y="2.5" width="8" height="5.5" fill="none" stroke="currentColor" stroke-width=".8"/><path d="M1 2.5l4 3 4-3" fill="none" stroke="currentColor" stroke-width=".8"/></symbol>
    <symbol id="icon-globe" viewBox="0 0 10 10"><circle cx="5" cy="5" r="4" fill="none" stroke="currentColor" stroke-width=".8"/><path d="M1 5h8M5 1c-2 2.5-2 5.5 0 8M5 1c2 2.5 2 5.5 0 8" fill="none" stroke="currentColor" stroke-width=".7"/></symbol>
  </defs>
</svg>

<!-- Chairs Filled Fast: large -->
<section class="card card--booking" style="left:619px;top:25px">
  <div class="panel">
    <svg class="panel-deco" viewBox="0 0 100 100" preserveAspectRatio="none"><path d="M0 0H40Q25 40 0 45Z" fill="#f3d9cd"/><path d="M50 0Q55 50 100 50V0Z" fill="var(--salmon)"/><path d="M58 0Q65 38 100 40V0Z" fill="#fff"/><path d="M0 80Q25 90 30 100H0Z" fill="var(--salmon)"/></svg>
    <div class="art" role="img" aria-label="Illustration of a woman relaxing with a laptop beside a potted plant"></div>
    <div class="brand-row"><span class="brand-name">Bloom Beauty Hub</span><span class="handle" style="margin-right:120px">@bloombeautyhub</span></div>
    <h2 class="heading">Chairs Filled<br>Fast</h2>
    <p class="subtitle">Attract more clients with simple,<br>strategic digital marketing.</p>
    <p class="body-copy">Chairs Filled Fast educates on the ins and outs of sponsored social media ads. With easy-to-follow video training, you’ll establish your online presence and increase salon bookings. Learn how to show up on social media with effective strategies that work. Choose our Handled Entirely system, or learn to do it all with our DIY system.</p>
    <div class="contact"><span><svg><use href="#icon-phone"/></svg>(+614) 1800 5521</span><span><svg><use href="#icon-mail"/></svg>hello@bloombeautyhub.com</span><span><svg><use href="#icon-globe"/></svg>www.bloombeautyhub.com</span></div>
  </div>
</section>

<!-- Chairs Filled Fast: narrow -->
<section class="card card--booking card--narrow" style="left:945px;top:25px">
  <div class="panel">
    <svg class="panel-deco" viewBox="0 0 100 100" preserveAspectRatio="none"><path d="M0 0H40Q25 40 0 45Z" fill="#f3d9cd"/><path d="M45 0Q50 45 100 45V0Z" fill="var(--salmon)"/><path d="M55 0Q62 34 100 36V0Z" fill="#fff"/><path d="M0 82Q20 90 25 100H0Z" fill="var(--salmon)"/></svg>
    <div class="art" role="img" aria-label="Illustration of a woman relaxing with a laptop beside a potted plant"></div>
    <div class="brand-row" style="justify-content:flex-start;gap:8px"><span class="brand-name">Bloom Beauty Hub</span><span class="handle">@bloombeautyhub</span></div>
    <h2 class="heading">Chairs Filled<br>Fast</h2>
    <p class="subtitle">Attract more clients with simple, strategic digital marketing.</p>
    <p class="body-copy">Chairs Filled Fast educates on the ins and outs of sponsored social media ads. With easy-to-follow video training, you’ll establish your online presence and increase salon bookings.<br>Learn how to show up on social media with effective strategies that work. Choose our Handled Entirely system, or learn to do it all with our DIY system.</p>
    <div class="contact"><span><svg><use href="#icon-phone"/></svg>(+614) 1800 5521</span><span><svg><use href="#icon-mail"/></svg>hello@bloombeautyhub.com</span><span><svg><use href="#icon-globe"/></svg>www.bloombeautyhub.com</span></div>
  </div>
</section>

<!-- Launch Pad Parlour: large -->
<section class="card card--start" style="left:24px;top:359px">
  <div class="panel">
    <svg class="panel-deco" viewBox="0 0 100 100" preserveAspectRatio="none"><path d="M0 0H55Q30 15 0 35Z" fill="#f8f0e8"/><path d="M0 40Q10 60 0 80Z" fill="var(--peach)"/><path d="M55 100Q75 75 100 80V100Z" fill="#f8f0e8"/></svg>
    <div class="brand-row"><span class="brand-name">Bloom Beauty Hub</span><span class="handle">@bloombeautyhub</span></div>
    <h2 class="heading">Launch Pad Parlour</h2>
    <p class="subtitle">Make your dream of owning a salon a reality.</p>
    <div class="art" role="img" aria-label="Illustration of a woman in a towel wrap enjoying a skincare treatment framed by leaves"></div>
    <p class="body-copy">Three options of start-up training and support, teaching must-know insights for beauty therapists who are ready to take the leap to salon owner and want to do it right. Whether you’ve been in the beauty industry a short time or forever, Launch Pad Parlour will set you up for salon success.</p>
    <div class="contact"><span><svg><use href="#icon-phone"/></svg>(+614) 1800 5521</span><span><svg><use href="#icon-mail"/></svg>hello@bloombeautyhub.com</span><span><svg><use href="#icon-globe"/></svg>www.bloombeautyhub.com</span></div>
  </div>
</section>

<!-- Launch Pad Parlour: narrow -->
<section class="card card--start card--narrow" style="left:357px;top:359px">
  <div class="panel">
    <svg class="panel-deco" viewBox="0 0 100 100" preserveAspectRatio="none"><path d="M0 0H60Q30 15 0 35Z" fill="#f8f0e8"/><path d="M0 45Q12 60 0 78Z" fill="var(--peach)"/><path d="M50 100Q75 75 100 80V100Z" fill="#f8f0e8"/></svg>
    <div class="brand-row"><span class="brand-name">Bloom Beauty Hub</span><span class="handle">@bloombeautyhub</span></div>
    <h2 class="heading">Launch Pad Parlour</h2>
    <p class="subtitle">Make your dream of owning a salon a reality.</p>
    <div class="art" role="img" aria-label="Illustration of a woman in a towel wrap enjoying a skincare treatment framed by leaves"></div>
    <p class="body-copy">Three options of start-up training and support, teaching must-know insights for beauty therapists who are ready to take the leap to salon owner and want to do it right. Whether you’ve been in the beauty industry a short time or forever, Launch Pad Parlour will set you up for salon success.</p>
    <div class="contact"><span><svg><use href="#icon-phone"/></svg>(+614) 1800 5521</span><span><svg><use href="#icon-mail"/></svg>hello@bloombeautyhub.com</span><span><svg><use href="#icon-globe"/></svg>www.bloombeautyhub.com</span></div>
  </div>
</section>

<!-- Revive Parlour Path: large -->
<section class="card card--revive" style="left:612px;top:359px">
  <div class="panel">
    <svg class="panel-deco" viewBox="0 0 100 100" preserveAspectRatio="none"><path d="M70 0Q85 15 100 30V0Z" fill="var(--salmon)"/><path d="M100 20Q75 25 85 55Q95 70 100 70Z" fill="#f0c9b6"/><path d="M0 88Q30 80 60 100H0Z" fill="#f0c9b6"/></svg>
    <div class="art" role="img" aria-label="Illustration of a woman holding a number one trophy beside a hashtag and a plant"></div>
    <div class="brand-row"><span class="brand-name">Bloom Beauty Hub</span><span class="handle">@bloombeautyhub</span></div>
    <h2 class="heading">Revive<br>Parlour Path</h2>
    <p class="subtitle">Successfully put your salon back on the <b>MAP</b>.</p>
    <p class="body-copy">Step into today’s beauty landscape with optimised marketing and industry expertise. If your salon’s been open for a year or even twenty years, Revive Parlour Path will elevate your business, renew your love for your salon and set you up to generate more income. Stand out from the competition as you increase online presence, learn key business development processes and see real results.</p>
    <div class="contact" style="--foot:var(--rose);font-weight:600"><span><svg><use href="#icon-phone"/></svg>(+614) 1800 5521</span><span><svg><use href="#icon-mail"/></svg>hello@bloombeautyhub.com</span><span><svg><use href="#icon-globe"/></svg>www.bloombeautyhub.com</span></div>
  </div>
</section>

<!-- Revive Parlour Path: narrow -->
<section class="card card--revive card--narrow" style="left:945px;top:359px">
  <div class="panel">
    <svg class="panel-deco" viewBox="0 0 100 100" preserveAspectRatio="none"><path d="M70 0Q85 15 100 30V0Z" fill="var(--salmon)"/><path d="M100 18Q70 25 82 55Q95 68 100 68Z" fill="#f0c9b6"/><path d="M0 90Q30 82 55 100H0Z" fill="#f0c9b6"/></svg>
    <div class="art" role="img" aria-label="Illustration of a woman holding a number one trophy beside a hashtag and a plant"></div>
    <div class="brand-row"><span class="brand-name">Bloom Beauty Hub</span><span class="handle">@bloombeautyhub</span></div>
    <h2 class="heading">Revive<br>Parlour Path</h2>
    <p class="subtitle">Successfully put your salon back on the <b>MAP</b>.</p>
    <p class="body-copy">Step into today’s beauty landscape with optimised marketing and industry expertise. If your salon’s been open for a year or even twenty years, Revive Parlour Path will elevate your business, renew your love for your salon and set you up to generate more income. Stand out from the competition as you increase online presence, learn key business development processes and see real results.</p>
    <div class="contact" style="--foot:var(--rose);font-weight:600"><span><svg><use href="#icon-phone"/></svg>(+614) 1800 5521</span><span><svg><use href="#icon-mail"/></svg>hello@bloombeautyhub.com</span><span><svg><use href="#icon-globe"/></svg>www.bloombeautyhub.com</span></div>
  </div>
</section>

<!-- Skillset Studio Plan: large -->
<section class="card card--educate" style="left:24px;top:693px">
  <div class="panel">
    <svg class="panel-deco" viewBox="0 0 100 100" preserveAspectRatio="none"><path d="M0 0H95Q90 18 55 18Q30 22 25 45Q10 50 0 48Z" fill="var(--pink-soft)"/><path d="M100 38Q70 40 60 65Q55 85 70 100H100Z" fill="var(--pink-soft)"/></svg>
    <div class="brand-row"><span class="brand-name">Bloom Beauty Hub</span><span class="handle">@bloombeautyhub</span></div>
    <h2 class="heading">Skillset Studio Plan</h2>
    <p class="subtitle">Successfully Upskill and Level Up Your Salon.</p>
    <div class="art" role="img" aria-label="Illustration of a woman climbing tall cylinder pillars with a ladder and a plant"></div>
    <p class="body-copy">Skillset Studio Plan offers three training options- In Salon, Online &amp; Diploma of Beauty Therapy. Whether you have your own salon or want to become qualified, Bloom Beauty Hub’s- Skillset Studio Plan adds industry authority and brings specialist expertise to all level of beauty therapists.<br>Our coaching is based in Australia, aim at female beauty salon owners who are ready to take their business to the next level.</p>
    <div class="contact"><span><svg><use href="#icon-phone"/></svg>(+614) 1800 5521</span><span><svg><use href="#icon-mail"/></svg>hello@bloombeautyhub.com</span><span><svg><use href="#icon-globe"/></svg>www.bloombeautyhub.com</span></div>
  </div>
</section>

<!-- Skillset Studio Plan: narrow -->
<section class="card card--educate card--narrow" style="left:357px;top:693px">
  <div class="panel">
    <svg class="panel-deco" viewBox="0 0 100 100" preserveAspectRatio="none"><path d="M0 0H95Q90 15 55 14Q30 18 25 40Q10 45 0 44Z" fill="var(--pink-soft)"/><path d="M100 50Q70 52 62 72Q58 88 70 100H100Z" fill="var(--pink-soft)"/></svg>
    <div class="brand-row"><span class="brand-name">Bloom Beauty Hub</span><span class="handle">@bloombeautyhub</span></div>
    <h2 class="heading">Skillset Studio Plan</h2>
    <p class="subtitle">Successfully Upskill and Level Up Your Salon.</p>
    <div class="art" role="img" aria-label="Illustration of a woman climbing tall cylinder pillars with a ladder and a plant"></div>
    <p class="body-copy">Skillset Studio Plan offers three training options- In Salon, Online &amp; Diploma of Beauty Therapy. Whether you have your own salon or want to become qualified, Bloom Beauty Hub’s- Skillset Studio Plan adds industry authority and brings specialist expertise to all level of beauty therapists. Our coaching is based in Australia, aim at female beauty salon owners who are ready to take their business to the next level.</p>
    <div class="contact"><span><svg><use href="#icon-phone"/></svg>(+614) 1800 5521</span><span><svg><use href="#icon-mail"/></svg>hello@bloombeautyhub.com</span><span><svg><use href="#icon-globe"/></svg>www.bloombeautyhub.com</span></div>
  </div>
</section>

<!-- Momentum Studio Plan: large -->
<section class="card card--excel" style="left:612px;top:693px">
  <div class="panel">
    <svg class="panel-deco" viewBox="0 0 100 100" preserveAspectRatio="none"><path d="M60 0Q60 30 100 32V0Z" fill="var(--coral)"/><path d="M100 65Q75 70 80 100H100Z" fill="var(--butter-deep)"/></svg>
    <div class="brand-row"><span class="brand-name">Bloom Beauty Hub</span><span class="handle">@bloombeautyhub</span></div>
    <h2 class="heading">Momentum Studio Plan</h2>
    <p class="subtitle">Transform your salon and your life.</p>
    <div class="art" role="img" aria-label="Illustration of a salon client surrounded by a ring of beauty treatment icons"></div>
    <p class="body-copy">Our most tailored program, Momentum Studio Plan offers coaching memberships with Bloom Beauty Hub’s Founder- Belinda. With our results focused framework, you will upskill employees, improve the working environment of the salon and receive leading beauty industry training as we dive into the culture and mindset of your salon. With Belinda as your business mentor and biggest cheerleader get ready to achieve your business goals and move forward with rapid growth.</p>
    <div class="contact"><span><svg><use href="#icon-phone"/></svg>(+614) 1800 5521</span><span><svg><use href="#icon-mail"/></svg>hello@bloombeautyhub.com</span><span><svg><use href="#icon-globe"/></svg>www.bloombeautyhub.com</span></div>
  </div>
</section>

<!-- Momentum Studio Plan: narrow -->
<section class="card card--excel card--narrow" style="left:945px;top:693px">
  <div class="panel">
    <svg class="panel-deco" viewBox="0 0 100 100" preserveAspectRatio="none"><path d="M60 0Q60 28 100 30V0Z" fill="var(--coral)"/><path d="M100 65Q75 72 80 100H100Z" fill="var(--butter-deep)"/></svg>
    <div class="brand-row"><span class="brand-name">Bloom Beauty Hub</span><span class="handle">@bloombeautyhub</span></div>
    <h2 class="heading">Momentum Studio Plan</h2>
    <p class="subtitle">Transform your salon and your life.</p>
    <div class="art" role="img" aria-label="Illustration of a salon client surrounded by a ring of beauty treatment icons"></div>
    <p class="body-copy">Our most tailored program, Momentum Studio Plan offers coaching memberships with Bloom Beauty Hub’s Founder- Belinda. With our results focused framework, you will upskill employees, improve the working environment of the salon and receive leading beauty industry training as we dive into the culture and mindset of your salon. With Belinda as your business mentor and biggest cheerleader get ready to achieve your business goals and move forward with rapid growth.</p>
    <div class="contact"><span><svg><use href="#icon-phone"/></svg>(+614) 1800 5521</span><span><svg><use href="#icon-mail"/></svg>hello@bloombeautyhub.com</span><span><svg><use href="#icon-globe"/></svg>www.bloombeautyhub.com</span></div>
  </div>
</section>

</body>
</html>
```